Bright Harbor Web Design & Marketing

Will award a 2nd place prize of $100.00 if someone can come up with a logo to match this design!
Updates

Okay, I'm really looking to see some better designs here. What do you think will bring the best designs out? Please remember with all future submissions I'm looking for a cartoon style / illustrator style website. I'm not sure what the technical term is for it, so I uploaded some images in the brief.

Target Market(s)

Small Business Owners

Industry/Entity Type

Marketing

Logo Text

BrightHarbor.com

Number of Pages Required

1 page

Colors

Designer to choose colors to be used in the design.

Requirements
Must have
• Logo should say BrightHarbor.com I would like more than just a text logo. I want some sort of cool custom graphic / icon with it that will look nice on shirts/hats/etc

```html
<!DOCTYPE html>
<html lang="en">
<head>
<meta charset="utf-8">
<title>Bright Harbor Web Design &amp; Marketing</title>
<link rel="stylesheet" href="https://fonts.googleapis.com/css2?family=Cinzel:wght@400;700&family=Mali:wght@600&family=Open+Sans:wght@400;600;700&display=swap">
<style>
:root{
  --orange:#f7941d;
  --orange-dark:#e07c0b;
  --navy:#2b3a8c;
  --hero-a:#3a3f9e;
  --hero-b:#6c70c9;
  --ink:#222;
  --muted:#666;
  --line:#ddd;
  --dark:#1d2128;
  --teal:#1aa7c4;
  --blue:#1f6fb2;
  --pale-blue:#e6eff9;
  --cream:#f7f5f0;
  --white:#fff;
}
*{box-sizing:border-box;margin:0;padding:0}
html,body{width:1200px;height:4675px;overflow:hidden}
body{font-family:"Open Sans",sans-serif;color:var(--ink);background:var(--white);position:relative}
section,header,footer{position:absolute;left:0;width:1200px;overflow:hidden}
.title{font-family:"Cinzel",serif;text-align:center;font-size:30px;letter-spacing:1px;color:var(--ink)}
.lead{font-size:13px;color:var(--muted);text-align:center;line-height:1.6;width:900px;margin:14px auto 0}
.brand{display:flex;align-items:center;gap:10px;font-family:"Open Sans",sans-serif;font-weight:700;color:var(--white);font-size:24px}
.brand-dot{width:34px;height:34px;border-radius:50%;background:var(--orange)}

/* hero */
.hero{top:0;height:592px;background:linear-gradient(180deg,var(--hero-a),var(--hero-b))}
.nav-bar{position:absolute;top:0;left:0;width:1200px;height:93px;background:rgba(30,34,110,.55)}
.nav-bar .brand{position:absolute;left:145px;top:28px}
.nav{position:absolute;right:90px;top:0;display:flex;list-style:none}
.nav li{width:95px;height:93px;display:flex;flex-direction:column;align-items:center;justify-content:flex-end;padding-bottom:20px;color:var(--white);font-size:12px;gap:8px}
.nav li.active{background:var(--orange)}
.nav li:nth-child(2){width:140px}
.nav-icon{width:20px;height:18px;border-radius:3px;background:rgba(255,255,255,.9)}
.hero h1{position:absolute;left:145px;top:150px;font-family:"Mali",cursive;color:var(--white);font-size:52px;line-height:64px;font-weight:600}
.hero-btns{position:absolute;left:145px;top:500px;display:flex;gap:14px}
.btn{display:inline-flex;align-items:center;gap:6px;height:38px;padding:0 16px;font-size:14px;color:var(--white);border-radius:3px}
.btn-orange{background:var(--orange)}
.btn-grey{background:#555}
.hero-art{position:absolute;left:700px;top:100px;width:420px;height:470px;border-radius:20px;background:linear-gradient(160deg,#f1c27a,#e9d84a 60%,#7a5fc0)}
.slider-arrow{position:absolute;top:350px;width:18px;height:24px;background:#333}

/* about */
.about{top:592px;height:203px;padding-top:60px}
.about .title span{color:var(--orange)}
.about .lead{font-family:Georgia,serif;text-align:left;width:980px;font-size:12px}

/* services */
.services{top:795px;height:810px;background:linear-gradient(180deg,#2a2f38,#1d232b 60%,#2f3a2a)}
.services .title{color:var(--white);margin-top:80px}
.services .lead{color:#ccc;font-size:12px}
.services svg{position:absolute;left:0;top:0}

/* plans */
.plans{top:1605px;height:670px;background:linear-gradient(180deg,#fff 0,#fff 62%,#c58a52 62%,#8c5a30)}
.plans .title{margin-top:60px}
.plan-row{position:absolute;top:140px;left:162px;display:flex;gap:25px}
.plan{width:206px;height:490px;background:var(--white);border-top:5px solid var(--orange);box-shadow:0 2px 8px rgba(0,0,0,.2);text-align:center;padding-top:26px;position:relative}
.plan:nth-child(2),.plan:nth-child(4){top:-8px}
.plan-icon{width:54px;height:54px;border-radius:50%;margin:0 auto;border:2px solid var(--orange);display:flex;align-items:center;justify-content:center}
.plan-icon i{width:22px;height:22px;background:var(--blue);border-radius:4px}
.plan h3{font-size:16px;font-weight:400;margin-top:22px}
.plan .from{font-size:10px;color:#999;margin-top:26px}
.plan .price{font-size:40px;color:var(--orange);margin-top:2px}
.plan .price sup,.plan .price small{font-size:14px}
.plan ul{list-style:none;text-align:left;margin:22px 0 0 26px;font-size:11px;color:#555}
.plan li{padding:8px 0;border-bottom:1px solid #eee;width:160px}
.plan li::before{content:"› ";color:var(--orange)}
.plan .btn{margin-top:26px;height:32px;font-size:12px;background:#444}
.plan.basic .btn{background:var(--orange)}
.plan .more{font-size:11px;margin-top:12px;color:#333}

/* video */
.video{top:2275px;height:593px;background:linear-gradient(180deg,#e8eef4,#b9c6d4 55%,#cfcac2)}
.video .title{margin-top:60px;color:#111}
.laptop{position:absolute;left:405px;top:160px;width:390px;height:260px;background:#1a1a1a;border-radius:14px;padding:14px}
.laptop-screen{width:100%;height:100%;background:linear-gradient(135deg,#5b68a8,#7b88c6);display:flex;align-items:center;justify-content:center;gap:10px;color:var(--white);font-weight:700;font-size:22px}
.play{width:46px;height:46px;border-radius:50%;background:var(--white);display:flex;align-items:center;justify-content:center}
.laptop-base{position:absolute;left:360px;top:420px;width:480px;height:14px;background:#bbb;border-radius:0 0 20px 20px}
.video-band{position:absolute;bottom:0;left:0;width:1200px;height:125px;background:rgba(20,20,20,.85);color:var(--white);font-family:Georgia,serif;font-size:16px;text-align:center;padding:38px 160px 0;line-height:1.6;letter-spacing:.5px}

/* clients */
.clients{top:2868px;height:265px;background:var(--cream)}
.clients .title{margin-top:44px}
.client-row{position:absolute;top:180px;left:105px;width:990px;display:flex;justify-content:space-between;align-items:center}
.client{display:flex;align-items:center;gap:6px;font-size:15px;font-weight:700;color:#333}
.client i{width:14px;height:14px;border-radius:50%;background:#333}
.chev{font-size:26px;color:#999}

/* why */
.why{top:3133px;height:483px;background:var(--pale-blue)}
.why .title{margin-top:60px}
.why svg{position:absolute;left:0;top:0}
.feature{position:absolute;width:250px;font-size:11px;color:#444;line-height:1.5}
.feature b{display:block;font-size:13px;color:var(--blue);font-weight:600}
.feature.r{text-align:right}

/* team */
.team{top:3616px;height:374px;background:var(--white)}
.team .title{margin-top:50px}
.member{position:absolute;top:232px;width:430px;height:110px;border:1px solid var(--line);padding:14px 16px;display:flex;gap:14px}
.avatar{width:60px;height:62px;background:linear-gradient(180deg,#9aa7b8,#5d6a7c);flex:none}
.member h4{font-size:13px;font-weight:700}
.member em{font-size:12px;color:var(--blue);font-style:normal}
.member p{font-size:11px;color:#555;margin-top:10px;line-height:1.5}

/* inquiry */
.inquiry{top:3990px;height:374px;background:#f4f4f4}
.inquiry-art{position:absolute;left:0;top:0;width:470px;height:374px;background:linear-gradient(120deg,#e8e4de,#c9c4bb)}
.inquiry .title{position:absolute;left:483px;width:530px;top:24px}
.form{position:absolute;left:483px;top:100px;width:530px;font-size:11px;color:#555}
.field{position:absolute;border-bottom:1px solid #bbb;height:34px;width:255px;padding-top:4px}
.field.box{height:72px;width:530px;border:1px solid #bbb;padding:4px}
.submit{position:absolute;top:264px;left:0;height:28px;padding:0 14px;background:var(--blue);color:var(--white);font-size:11px;display:flex;align-items:center}

/* footer */
.footer{top:4364px;height:281px;background:linear-gradient(180deg,#1f2530,#12161d);color:#ddd}
.col{position:absolute;top:50px;font-size:11px;line-height:1.9}
.col h5{font-size:13px;font-weight:600;color:var(--white);margin-bottom:10px}
.col h5 span{color:var(--orange)}
.col ul{list-style:none}
.col li::before{content:"› "}
.news-input{width:210px;height:26px;background:var(--white);margin-top:12px;color:#999;padding:4px 8px}
.news-btn{width:100px;height:26px;background:var(--blue);color:var(--white);margin-top:10px;text-align:center;padding-top:4px}
.footer-mark{position:absolute;right:120px;top:60px;display:flex;flex-direction:column;align-items:center;gap:10px;color:var(--white);font-weight:700;font-size:16px}
.footer-mark i{width:110px;height:110px;border-radius:50%;background:rgba(255,255,255,.85)}
.copy{top:4645px;height:30px;background:#0b0d11;color:#aaa;font-size:11px;display:flex;justify-content:space-between;align-items:center;padding:0 145px}
</style>
</head>
<body>

<header class="hero">
  <div class="nav-bar">
    <div class="brand"><span class="brand-dot"></span>BrightHarbor.com</div>
    <ul class="nav">
      <li class="active"><span class="nav-icon"></span>HOME</li>
      <li><span class="nav-icon"></span>SERVICES &amp; PRICING</li>
      <li><span class="nav-icon"></span>OUR TEAM</li>
      <li><span class="nav-icon"></span>CLIENTS</li>
      <li><span class="nav-icon"></span>CONTACT US</li>
    </ul>
  </div>
  <h1>The Design &amp;<br>Marketing Team<br>That Always Puts<br>Trust &amp; Loyalty<br>Before Profits</h1>
  <div class="hero-btns">
    <span class="btn btn-orange">&#9998; Read More</span>
    <span class="btn btn-grey">&#9742; Call Us Today</span>
  </div>
  <div class="hero-art" role="img" aria-label="Cartoon dog working at a computer desk"></div>
  <span class="slider-arrow" style="left:0"></span>
  <span class="slider-arrow" style="right:0"></span>
</header>

<section class="about">
  <h2 class="title">About <span>Bright Harbor</span></h2>
  <p class="lead">We believe that honesty and integrity come before personal profit. We are a family owned and operated company who take care of each other and that is exactly what we have always done. We treat each of our clients with the same loyalty and respect that we give each other.<br>We are not looking to have hundreds and hundreds of clients. We are looking to expand our family with a handful of like minded people and companies who take pride in their work and their customers. We want to build mutually beneficial, lucrative and long term partnerships.</p>
</section>

<section class="services" role="img" aria-label="Dark illustrated city scene behind a diagram of services">
  <h2 class="title">Services We Provide</h2>
  <p class="lead">Lorem ipsum dolor sit amet, consectetuer adipiscing elit, sed diam nonummy nibh euismod tincidunt ut laoreet dolore magna aliquam erat volutpat. Ut wisi enim ad minim veniam, quis nostrud exerci.</p>
  <svg width="1200" height="810" viewBox="0 0 1200 810" font-family="Open Sans, sans-serif">
    <g stroke="#8a9bb0" stroke-width="2" fill="none">
      <circle cx="600" cy="410" r="150" stroke-dasharray="4 6"/>
      <line x1="600" y1="410" x2="530" y2="300"/><line x1="600" y1="410" x2="670" y2="300"/>
      <line x1="600" y1="410" x2="740" y2="360"/><line x1="600" y1="410" x2="745" y2="460"/>
      <line x1="600" y1="410" x2="690" y2="530"/><line x1="600" y1="410" x2="600" y2="560"/>
      <line x1="600" y1="410" x2="470" y2="530"/><line x1="600" y1="410" x2="440" y2="420"/>
    </g>
    <circle cx="600" cy="410" r="60" fill="#fff"/>
    <circle cx="600" cy="410" r="20" fill="#1d232b"/>
    <g font-size="11" fill="#fff" font-weight="700">
      <circle cx="530" cy="290" r="38" fill="#f7941d"/><circle cx="490" cy="320" r="13" fill="#f7941d"/><text x="486" y="324">1</text>
      <circle cx="670" cy="290" r="38" fill="#1aa7c4"/><circle cx="715" cy="310" r="13" fill="#1aa7c4"/><text x="711" y="314">2</text>
      <circle cx="755" cy="350" r="34" fill="#8bc34a"/><circle cx="795" cy="375" r="13" fill="#8bc34a"/><text x="791" y="379">3</text>
      <circle cx="755" cy="460" r="34" fill="#9c4fd4"/><circle cx="770" cy="500" r="13" fill="#9c4fd4"/><text x="766" y="504">4</text>
      <circle cx="690" cy="540" r="34" fill="#e53935"/><circle cx="680" cy="585" r="13" fill="#e53935"/><text x="676" y="589">5</text>
      <circle cx="600" cy="570" r="32" fill="#1f6fb2"/><circle cx="640" cy="600" r="13" fill="#1f6fb2"/><text x="636" y="604">6</text>
      <circle cx="470" cy="540" r="34" fill="#26a69a"/><circle cx="490" cy="580" r="13" fill="#26a69a"/><text x="486" y="584">7</text>
      <circle cx="405" cy="420" r="34" fill="#cddc39"/><circle cx="395" cy="460" r="13" fill="#cddc39"/><text x="391" y="464">8</text>
    </g>
    <g font-size="11" fill="#fff">
      <text x="340" y="225" fill="#f7941d" font-weight="700">Consulting Service</text>
      <text x="340" y="241">Duis autem vel eum iriure</text><text x="340" y="255">dolor in hendrerit in vulputate</text>
      <text x="725" y="225" fill="#1aa7c4" font-weight="700">Website Design &amp; Management</text>
      <text x="725" y="241">Duis autem vel eum iriure</text><text x="725" y="255">dolor in hendrerit in vulputate</text>
      <text x="830" y="320" fill="#8bc34a" font-weight="700">Logo Design &amp; Branding Materials</text>
      <text x="830" y="336">Duis autem vel eum iriure</text><text x="830" y="350">dolor in hendrerit in vulputate</text>
      <text x="830" y="430" fill="#b07be0" font-weight="700">Online Design &amp; Marketing</text>
      <text x="830" y="446">Duis autem vel eum iriure</text><text x="830" y="460">dolor in hendrerit in vulputate</text>
      <text x="740" y="600" fill="#e53935" font-weight="700">Local Seo Management</text>
      <text x="740" y="616">Duis autem vel eum iriure</text><text x="740" y="630">dolor in hendrerit in vulputate</text>
      <text x="570" y="670" fill="#4fa3e0" font-weight="700">Search Engine Optimization</text>
      <text x="570" y="686">Duis autem vel eum iriure dolor</text>
      <text x="235" y="565" fill="#26a69a" font-weight="700">Social Media Marketing</text>
      <text x="235" y="581">Duis autem vel eum iriure</text><text x="235" y="595">dolor in hendrerit in vulputate</text>
      <text x="140" y="440" fill="#cddc39" font-weight="700">Marketing Material &amp; Print Design</text>
      <text x="140" y="456">Duis autem vel eum iriure</text><text x="140" y="470">dolor in hendrerit in vulputate</text>
      <text x="205" y="320" fill="#f7941d" font-weight="700">Outsourcing Management</text>
      <text x="205" y="336">Duis autem vel eum iriure</text><text x="205" y="350">dolor in hendrerit in vulputate</text>
    </g>
  </svg>
</section>

<section class="plans">
  <h2 class="title">Select Your Plan</h2>
  <div class="plan-row">
    <div class="plan basic">
      <div class="plan-icon"><i></i></div>
      <h3>Basic Plan</h3><p class="from">Starting from</p>
      <p class="price"><sup>$</sup>52<small>.95</small></p>
      <ul><li>Lorem Ipsum Dolor Sit</li><li>Lorem Ipsum Dolor Sit</li><li>Lorem Ipsum Dolor Sit</li><li>Lorem Ipsum Dolor Sit</li><li>Lorem Ipsum Dolor Sit</li></ul>
      <span class="btn">Get Started &rarr;</span><p class="more">More Information</p>
    </div>
    <div class="plan">
      <div class="plan-icon"><i></i></div>
      <h3>Standard Plan</h3><p class="from">Starting from</p>
      <p class="price"><sup>$</sup>114<small>.95</small></p>
      <ul><li>Lorem Ipsum Dolor Sit</li><li>Lorem Ipsum Dolor Sit</li><li>Lorem Ipsum Dolor Sit</li><li>Lorem Ipsum Dolor Sit</li><li>Lorem Ipsum Dolor Sit</li></ul>
      <span class="btn">Get Started &rarr;</span><p class="more">More Information</p>
    </div>
    <div class="plan">
      <div class="plan-icon"><i></i></div>
      <h3>Gold Plan</h3><p class="from">Starting from</p>
      <p class="price"><sup>$</sup>200<small>.95</small></p>
      <ul><li>Lorem Ipsum Dolor Sit</li><li>Lorem Ipsum Dolor Sit</li><li>Lorem Ipsum Dolor Sit</li><li>Lorem Ipsum Dolor Sit</li><li>Lorem Ipsum Dolor Sit</li></ul>
      <span class="btn">Get Started &rarr;</span><p class="more">More Information</p>
    </div>
    <div class="plan">
      <div class="plan-icon"><i></i></div>
      <h3>Platinum Plan</h3><p class="from">Starting from</p>
      <p class="price"><sup>$</sup>490<small>.95</small></p>
      <ul><li>Lorem Ipsum Dolor Sit</li><li>Lorem Ipsum Dolor Sit</li><li>Lorem Ipsum Dolor Sit</li><li>Lorem Ipsum Dolor Sit</li><li>Lorem Ipsum Dolor Sit</li></ul>
      <span class="btn">Get Started &rarr;</span><p class="more">More Information</p>
    </div>
  </div>
</section>

<section class="video" role="img" aria-label="City skyline and desk scene around a laptop">
  <h2 class="title">Watch Video</h2>
  <div class="laptop"><div class="laptop-screen"><span class="play">&#9654;</span>BrightHarbor.com</div></div>
  <div class="laptop-base"></div>
  <p class="video-band">LOREM IPSUM DOLOR SIT AMET, CONSECTETUER ADIPISCING ELIT, SED DIAM NONUMMY NIBH EUISMOD TINCIDUNT UT LAOREET DOLORE MAGNA ALIQUAM ERAT VOLUTPAT</p>
</section>

<section class="clients">
  <h2 class="title">Our Clients</h2>
  <p class="lead">Lorem ipsum dolor sit amet, consectetuer adipiscing elit, sed diam nonummy nibh euismod tincidunt ut laoreet dolore magna aliquam erat volutpat. Ut wisi enim ad minim veniam, quis nostrud exerci.</p>
  <div class="client-row">
    <span class="chev">&lsaquo;</span>
    <span class="client"><i></i>Maplecrest</span>
    <span class="client">Northwall</span>
    <span class="client">Northwall</span>
    <span class="client">Tidepoint</span>
    <span class="client"><i></i>Maplecrest</span>
    <span class="client"><i></i>Solvane</span>
    <span class="client">Keystack</span>
    <span class="client">Keystack</span>
    <span class="chev">&rsaquo;</span>
  </div>
</section>

<section class="why">
  <h2 class="title">Why Choose Us</h2>
  <p class="lead">Lorem ipsum dolor sit amet, consectetuer adipiscing elit, sed diam nonummy nibh euismod tincidunt ut laoreet dolore magna aliquam erat volutpat. Ut wisi enim ad minim veniam, quis nostrud exerci.</p>
  <svg width="1200" height="483" viewBox="0 0 1200 483">
    <path d="M470 220 A140 140 0 0 1 730 220" fill="none" stroke="#9fb6d0" stroke-width="2"/>
    <path d="M470 260 A140 140 0 0 0 730 260" fill="none" stroke="#9fb6d0" stroke-width="2"/>
    <circle cx="600" cy="230" r="58" fill="#1f6fb2"/>
    <circle cx="600" cy="230" r="44" fill="none" stroke="#fff" stroke-width="3"/>
    <circle cx="470" cy="240" r="18" fill="#f7941d"/>
    <circle cx="730" cy="240" r="18" fill="#1f6fb2"/>
    <circle cx="515" cy="335" r="18" fill="#1aa7c4"/>
    <circle cx="685" cy="335" r="18" fill="#1f6fb2"/>
    <circle cx="600" cy="370" r="18" fill="#1aa7c4"/>
  </svg>
  <div class="feature r" style="left:200px;top:225px"><b>100% Risk Free Investment</b>Lorem ipsum dolor sit amet, consectetuer adipiscing elit, sed diam.</div>
  <div class="feature r" style="left:245px;top:320px"><b>Customer Loyalty Program</b>Lorem ipsum dolor sit amet, consectetuer adipiscing elit, sed diam.</div>
  <div class="feature" style="left:760px;top:225px"><b>Multiple Payment Options Available</b>Lorem ipsum dolor sit amet, consectetuer adipiscing elit, sed diam.</div>
  <div class="feature" style="left:715px;top:320px"><b>Unmatched Personal Service</b>Lorem ipsum dolor sit amet, consectetuer adipiscing elit, sed diam.</div>
  <div class="feature" style="left:475px;top:400px;text-align:center"><b>24/7 U.S. Based Customer Support</b>Lorem ipsum dolor sit amet, consectetuer adipiscing elit, sed diam.</div>
</section>

<section class="team">
  <h2 class="title">Our Team</h2>
  <p class="lead">Lorem ipsum dolor sit amet, consectetuer adipiscing elit, sed diam nonummy nibh euismod tincidunt ut laoreet dolore magna aliquam erat volutpat. Ut wisi enim ad minim veniam, quis nostrud exerci.</p>
  <span class="chev" style="position:absolute;left:110px;top:268px">&lsaquo;</span>
  <div class="member" style="left:150px">
    <div class="avatar" role="img" aria-label="Portrait photo of team member"></div>
    <div><h4>DANIEL CORWIN</h4><em>Chief Executive Officer</em><p>Lorem ipsum dolor sit amet, consectetuer adipiscing elit, sed diam nonummy nibh euismod tincidunt ut laoreet dolore magna aliquam [...]</p></div>
  </div>
  <div class="member" style="left:640px">
    <div class="avatar" role="img" aria-label="Portrait photo of team member"></div>
    <div><h4>OWEN PRATLEY</h4><em>Chief Operations Officer</em><p>Lorem ipsum dolor sit amet, consectetuer adipiscing elit, sed diam nonummy nibh euismod tincidunt ut laoreet dolore magna aliquam [...]</p></div>
  </div>
  <span class="chev" style="position:absolute;left:1080px;top:268px">&rsaquo;</span>
</section>

<section class="inquiry">
  <div class="inquiry-art" role="img" aria-label="Hands typing on a laptop beside a coffee cup"></div>
  <h2 class="title">Quick Inquiry</h2>
  <div class="form">
    <div class="field" style="left:0;top:0">First Name</div>
    <div class="field" style="left:275px;top:0">Last Name</div>
    <div class="field" style="left:0;top:50px">Email</div>
    <div class="field" style="left:275px;top:50px">Phone Number</div>
    <div class="field box" style="left:0;top:118px">Details About Your Enquiry</div>
    <span class="submit">SUBMIT</span>
  </div>
</section>

<footer class="footer" role="img" aria-label="Dark city skyline behind the footer">
  <div class="col" style="left:145px">
    <h5>Quick <span>Links</span></h5>
    <ul><li>Home</li><li>Services</li><li>Pricing</li><li>Our Team</li><li>Success Stories</li><li>Clients</li><li>Contact Us</li></ul>
  </div>
  <div class="col" style="left:340px">
    <h5>Contact <span>Details</span></h5>
    <p>BrightHarbor.com<br>48 Lantern Row<br>Fairhaven, OR 97000</p>
    <p>&#9742; (555) 014-2290<br>&#9742; (555) 014-2291<br>&#9993; hello@brightharbor.com</p>
  </div>
  <div class="col" style="left:610px">
    <h5>Newsletter <span>Signup</span></h5>
    <p>Lorem ipsum dolor sit amet, consectetuer<br>adipiscing elit, sed dia</p>
    <div class="news-input">Email</div>
    <div class="news-btn">Subscribe</div>
  </div>
  <div class="footer-mark"><i></i>BrightHarbor.com</div>
</footer>
<div class="copy" style="position:absolute;left:0;top:4645px;width:1200px"><span>Copyright &copy; 2017 BrightHarbor.com. All rights reserved</span><span>Terms of Use | Privacy Policy</span></div>

</body>
</html>
```